Landing page design for my current website

I need a landing page designed for my Wordpress website. My website is Velmorquay.com, and I need a page that will serve as a landing page for online ads I run. Please follow the color scheme of the current website

This web page will be targeted towards real estate owners who are looking for a property manager. Above the fold needs to have a CTA form headlined with "As a Rental Property Owner, I Want More Protection, Less Stress, and Drama-Free Living"

A few highlights that can be listed beyond the CTA and fold

- Comprehensive Property Management
Full-service management covering tenant placement, leasing, maintenance, and inspections.

Maximized Rental Income
Proven strategies to optimize rental rates and minimize vacancies, ensuring higher ROI.

Stress-Free Management
We handle all tenant interactions, maintenance requests, and property issues, so you don't have to.

Experienced Team
Over a decade of experience in managing single-family homes, small multifamily units, and apartment complexes.

Advanced Technology
Utilize cutting-edge property management software for efficient communication, rent collection, and maintenance tracking.

Tenant Screening and Placement
Thorough background checks and tenant screening processes to ensure reliable and responsible tenants.

Regular Property Inspections
Routine inspections to maintain property condition and address issues before they become costly problems.

Legal Compliance
Expertise in local and federal rental laws to keep your properties compliant and avoid legal hassles.

Transparent Reporting
Detailed monthly reports and financial statements to keep you informed about your property's performance.

Personalized Service
Tailored management plans to meet the unique needs of your properties and investment goals.
Effective Tenant Conflict Resolution
Skilled in handling challenging tenant situations, ensuring conflicts are resolved quickly and professionally to maintain a peaceful living environment and protect your investment.

```html
<!DOCTYPE html>
<html lang="en">
<head>
<meta charset="UTF-8">
<title>Velmorquay Realty – Property Management</title>
<link href="https://fonts.googleapis.com/css2?family=Poppins:wght@400;500;600;700&display=swap" rel="stylesheet">
<style>
:root{
  --navy:#0f3e78;
  --navy-dark:#0b2f5e;
  --footer:#0e3f77;
  --ink:#1e1e24;
  --muted:#5a5a62;
  --line:#d9dce2;
  --white:#ffffff;
}
*{box-sizing:border-box;margin:0;padding:0}
html,body{width:1200px;height:2889px;overflow:hidden;background:var(--white);font-family:'Poppins',sans-serif;color:var(--ink)}
.page{position:relative;width:1200px;height:2889px}

.hero{position:absolute;left:0;top:0;width:1200px;height:685px;
  background:linear-gradient(180deg,#3f6fae 0%,#7da3cf 28%,#c9cdd2 50%,#8a7a6a 72%,#4f7a34 88%,#3c6a2a 100%)}
.brand{position:absolute;display:flex;align-items:center;gap:10px;color:var(--white);font-weight:600;letter-spacing:.5px}
.brand-dot{width:40px;height:40px;border-radius:50%;border:3px solid var(--white)}
.hero .brand{left:110px;top:14px;font-size:22px}
.menu{position:absolute;left:1060px;top:24px;width:28px}
.menu span{display:block;height:3px;background:var(--white);margin-bottom:6px;border-radius:2px}
.hero-title{position:absolute;left:0;top:278px;width:1200px;text-align:center;color:var(--white);font-weight:700;text-shadow:0 3px 6px rgba(0,0,0,.55)}
.hero-title .small{display:block;font-size:38px;line-height:46px}
.hero-title .big{display:block;font-size:48px;line-height:62px}
.cta{position:absolute;left:482px;top:407px;width:236px;height:54px;border-radius:27px;background:var(--navy-dark);border:2px solid var(--white);display:flex;align-items:center;padding-left:42px;color:var(--white);font-weight:600;font-size:18px}
.cta-icon{position:absolute;right:8px;top:6px;width:40px;height:40px;border-radius:50%;background:var(--white);display:flex;align-items:center;justify-content:center}

.lead-card{position:absolute;left:111px;top:584px;width:977px;height:351px;background:var(--white);border:1px solid #e3e5ea;box-shadow:0 4px 14px rgba(0,0,0,.08)}
.lead-card h2{position:absolute;left:0;top:39px;width:100%;text-align:center;font-size:18px;font-weight:600;color:var(--ink);letter-spacing:.1px}
.field{position:absolute;width:265px}
.field label{display:block;font-size:13px;color:#333;margin-bottom:8px}
.field .input{height:50px;border:1px solid var(--line);border-radius:3px;padding:0 16px;display:flex;align-items:center;font-size:11px;color:#9a9ca3}
.send{position:absolute;left:358px;top:277px;width:263px;height:48px;background:var(--navy);color:var(--white);font-weight:600;font-size:17px;display:flex;align-items:center;justify-content:center;border-radius:2px}

.section-title{position:absolute;left:0;top:978px;width:1200px;text-align:center;font-size:30px;font-weight:700;color:var(--navy)}
.card{position:absolute;width:398px;height:227px;border:1px solid var(--line);border-radius:6px;background:var(--white)}
.card .icon{position:absolute;left:25px;top:29px;width:69px;height:69px;border-radius:50%;display:flex;align-items:center;justify-content:center}
.card .icon.blue{background:var(--navy)}
.card .icon.dark{background:#2b2b2e}
.card h3{position:absolute;left:123px;top:32px;width:260px;font-size:18px;font-weight:600;line-height:31px;white-space:nowrap}
.card h3.blue{color:var(--navy)}
.card h3.dark{color:var(--ink)}
.card p{position:absolute;left:25px;top:119px;width:355px;font-size:16px;line-height:28px;color:var(--muted)}

.footer{position:absolute;left:0;top:2417px;width:1200px;height:472px;background:var(--footer);color:var(--white)}
.footer .brand{left:0;width:1200px;justify-content:center;top:66px;font-size:22px}
.col{position:absolute;top:168px}
.col h4{font-size:24px;font-weight:600;margin-bottom:20px;letter-spacing:-.3px}
.col a{display:block;color:var(--white);text-decoration:none;font-size:18px;line-height:34.5px}
.contact-item{display:flex;align-items:center;gap:16px;font-size:18px;letter-spacing:1px;height:60px}
.divider{position:absolute;left:111px;top:404px;width:977px;height:1px;background:rgba(255,255,255,.7)}
.social{position:absolute;left:112px;top:430px;display:flex;gap:22px}
.social span{width:18px;height:18px;border:2px solid var(--white);border-radius:4px}
.copy{position:absolute;right:114px;top:428px;font-size:16px;letter-spacing:1px}
</style>
</head>
<body>
<div class="page">

  <header class="hero" role="img" aria-label="Photo of a modern two-storey white house with wood accents, lawn and trees under a blue sky">
    <div class="brand"><span class="brand-dot"></span>VELMORQUAY REALTY</div>
    <div class="menu"><span></span><span></span><span></span></div>
    <h1 class="hero-title"><span class="small">WELCOME TO</span><span class="big">VELMORQUAY REALTY</span></h1>
    <div class="cta">GET STARTED
      <span class="cta-icon"><svg width="20" height="20" viewBox="0 0 20 20"><path d="M10 2 L19 10 H16 V18 H12 V13 H8 V18 H4 V10 H1 Z" fill="#0b2f5e"/></svg></span>
    </div>
  </header>

  <section class="lead-card">
    <h2>AS A RENTAL PROPERTY OWNER, I WANT MORE PROTECTION, LESS STRESS, AND DRAMA-FREE LIVING</h2>
    <div class="field" style="left:67px;top:81px"><label>First Name</label><div class="input">Lorem ipsum</div></div>
    <div class="field" style="left:360px;top:81px"><label>Last&nbsp; Name</label><div class="input">Lorem ipsum</div></div>
    <div class="field" style="left:653px;top:81px"><label>Phone Number</label><div class="input">Lorem ipsum</div></div>
    <div class="field" style="left:67px;top:174px"><label>E-mail Address</label><div class="input">Lorem ipsum</div></div>
    <div class="field" style="left:360px;top:174px"><label>Your Home Address</label><div class="input">Lorem ipsum</div></div>
    <div class="field" style="left:653px;top:174px"><label>Message</label><div class="input">Lorem ipsum</div></div>
    <div class="send">SEND MESSAGE</div>
  </section>

  <h2 class="section-title">OUR HIGHLIGHS</h2>

  <article class="card" style="left:160px;top:1075px"><div class="icon blue"><svg width="30" height="30" viewBox="0 0 30 30"><circle cx="15" cy="15" r="9" fill="none" stroke="#fff" stroke-width="2.5"/><circle cx="15" cy="15" r="3" fill="#fff"/></svg></div><h3 class="blue">COMPREHENSIVE PROPERTY<br>MANAGEMENT</h3><p>Full-service management covering tenant placement, leasing, maintenance, and inspections.</p></article>
  <article class="card" style="left:643px;top:1075px"><div class="icon dark"><svg width="30" height="30" viewBox="0 0 30 30"><path d="M15 4 L27 14 H23 V26 H7 V14 H3 Z" fill="none" stroke="#fff" stroke-width="2.5"/></svg></div><h3 class="dark">MAXIMIZED RENTAL<br>INCOME</h3><p>Proven strategies to optimize rental rates and minimize vacancies, ensuring higher ROI.</p></article>

  <article class="card" style="left:160px;top:1337px"><div class="icon dark"><svg width="30" height="30" viewBox="0 0 30 30"><circle cx="15" cy="9" r="4" fill="#fff"/><path d="M7 26 C7 17 23 17 23 26 Z" fill="#fff"/></svg></div><h3 class="dark">STRESS-FREE<br>MANAGEMENT</h3><p>We handle all tenant interactions, maintenance requests, and property issues, so you don't have to.</p></article>
  <article class="card" style="left:643px;top:1337px"><div class="icon blue"><svg width="30" height="30" viewBox="0 0 30 30"><circle cx="15" cy="10" r="4" fill="#fff"/><path d="M7 26 C7 17 23 17 23 26 Z" fill="#fff"/></svg></div><h3 class="blue">OUR EXPERIENCED<br>TEAMS</h3><p>Over a decade of experience in managing single-family homes, small multifamily units, and apartment complexes.</p></article>

  <article class="card" style="left:160px;top:1598px"><div class="icon blue"><svg width="30" height="30" viewBox="0 0 30 30"><circle cx="13" cy="15" r="9" fill="none" stroke="#fff" stroke-width="2.5"/><path d="M18 15 H28 M24 11 L28 15 L24 19" fill="none" stroke="#fff" stroke-width="2.5"/></svg></div><h3 class="blue">OUR ADVANCED<br>TECHNOLOGY</h3><p>Utilize cutting-edge property management software for efficient communication, rent collection, and maintenance tracking.</p></article>
  <article class="card" style="left:643px;top:1598px"><div class="icon dark"><svg width="30" height="30" viewBox="0 0 30 30"><path d="M6 6 H24 V18 H6 Z" fill="none" stroke="#fff" stroke-width="2.5"/><path d="M10 12 L14 15 L20 9" fill="none" stroke="#fff" stroke-width="2.5"/><path d="M12 24 H18" stroke="#fff" stroke-width="2.5"/></svg></div><h3 class="dark">TENANT SCREENING AND<br>PLACEMENT</h3><p>Thorough background checks and tenant screening processes to ensure reliable and responsible tenants.</p></article>

  <article class="card" style="left:160px;top:1860px"><div class="icon dark"><svg width="30" height="30" viewBox="0 0 30 30"><path d="M13 5 L26 15 H23 V25 H14 V15 H11 Z" fill="none" stroke="#fff" stroke-width="2.5"/><circle cx="8" cy="17" r="3" fill="#fff"/><path d="M3 26 C3 20 13 20 13 26 Z" fill="#fff"/></svg></div><h3 class="dark">REGULAR PROPERTY<br>INSPECTIONS</h3><p>Routine inspections to maintain property condition and address issues before they become costly problems.</p></article>
  <article class="card" style="left:643px;top:1860px"><div class="icon blue"><svg width="30" height="30" viewBox="0 0 30 30"><path d="M6 4 H19 V26 H6 Z" fill="none" stroke="#fff" stroke-width="2.5"/><path d="M16 16 L23 13 L28 16 V20 C28 24 23 26 23 26 C23 26 18 24 18 20 Z" fill="#fff"/></svg></div><h3 class="blue">OUR LEGAL<br>COMPLIANCE</h3><p>Expertise in local and federal rental laws to keep your properties compliant and avoid legal hassles.</p></article>

  <article class="card" style="left:160px;top:2121px"><div class="icon blue"><svg width="30" height="30" viewBox="0 0 30 30"><path d="M6 4 H20 V26 H6 Z" fill="none" stroke="#fff" stroke-width="2.5"/><path d="M10 11 H16 M10 16 H16" stroke="#fff" stroke-width="2"/><circle cx="22" cy="22" r="5" fill="#fff"/></svg></div><h3 class="blue">OUR TRANSPARENT<br>REPORTING</h3><p>Detailed monthly reports and financial statements to keep you informed about your property's performance.</p></article>
  <article class="card" style="left:643px;top:2121px"><div class="icon dark"><svg width="30" height="30" viewBox="0 0 30 30"><circle cx="15" cy="15" r="10" fill="none" stroke="#fff" stroke-width="3.5" stroke-dasharray="4 2.5"/><circle cx="15" cy="15" r="4" fill="none" stroke="#fff" stroke-width="2.5"/></svg></div><h3 class="dark">OUR PERSONALIZED<br>SERVICE</h3><p>Tailored management plans to meet the unique needs of your properties and investment goals.</p></article>

  <footer class="footer">
    <div class="brand"><span class="brand-dot"></span>VELMORQUAY REALTY</div>

    <div class="col" style="left:109px">
      <h4>CONTACT US</h4>
      <div class="contact-item"><svg width="22" height="26" viewBox="0 0 22 26"><path d="M11 1 C5 1 2 5 2 10 C2 17 11 25 11 25 C11 25 20 17 20 10 C20 5 17 1 11 1 Z" fill="#fff"/><circle cx="11" cy="10" r="3.5" fill="#0e3f77"/></svg>Harlow Bay</div>
      <div class="contact-item"><svg width="22" height="18" viewBox="0 0 22 18"><rect x="1.5" y="1.5" width="19" height="15" rx="2" fill="none" stroke="#fff" stroke-width="2"/><path d="M2 3 L11 10 L20 3" fill="none" stroke="#fff" stroke-width="2"/></svg>hello@Velmorquay.com</div>
      <div class="contact-item"><svg width="22" height="22" viewBox="0 0 22 22"><path d="M5 2 L9 6 L7 9 C8 12 10 14 13 15 L16 13 L20 17 L17 20 C9 20 2 13 2 5 Z" fill="none" stroke="#fff" stroke-width="1.8"/></svg>555.014.2270</div>
    </div>

    <div class="col" style="left:434px">
      <h4>MAIN LINKS</h4>
      <a>Home</a><a>For Investors</a><a>Residents</a><a>Contact</a>
    </div>
    <div class="col" style="left:633px">
      <h4>SERVICE AREAS</h4>
      <a>Bloomsburg</a><a>Danville</a><a>Berwick</a><a>Williamsport</a>
    </div>
    <div class="col" style="left:862px">
      <h4>OTHER RESOURCES</h4>
      <a>Active Rentals</a><a>Rent Pay</a>
    </div>

    <div class="divider"></div>
    <div class="social"><span></span><span></span><span></span><span></span><span></span></div>
    <div class="copy">Copyright © 2024 Velmorquay Realty. All Rights Reserved</div>
  </footer>

</div>
</body>
</html>
```